Tolbek cards

I want a simple business card that pops.
Logo on one side.
On side two i want.
"Are you thinking about a new building on your property, or renovating an existing structure? Contact".....
Owners Name: Dale Whitacre
Owners Phone number: 610-555-0187
Address:4076 Copper Ridge RD, Carvell, OH 43912
Committed to Quality, Service, and Integrity

```html
<!DOCTYPE html>
<html lang="en">
<head>
<meta charset="utf-8">
<title>Tolbek Builders LLC – Business Cards</title>
<link rel="stylesheet" href="https://fonts.googleapis.com/css2?family=Poppins:wght@400;600&display=swap">
<style>
  :root{
    --brown:#432e1d;
    --paper:#ffffff;
    --backdrop:#f2f2f2;
    --ink:#1a1410;
  }
  *{box-sizing:border-box;margin:0;padding:0}
  html,body{width:1200px;height:960px;overflow:hidden;background:var(--backdrop);font-family:"Poppins",sans-serif}
  .card{position:absolute;top:112px;width:420px;height:735px;border-radius:30px;box-shadow:0 14px 34px rgba(0,0,0,.28)}
  .card--front{left:149px;background:var(--brown)}
  .card--back{left:628px;background:var(--paper);color:var(--ink);text-align:center}

  .front-mark{position:absolute;left:50%;top:50%;display:flex;align-items:center;gap:22px;transform:translate(-50%,-50%) rotate(-90deg);color:var(--paper);font-weight:600}
  .front-mark__dot{width:64px;height:64px;border-radius:50%;background:var(--paper)}
  .front-mark__name{display:flex;flex-direction:column;line-height:1}
  .front-mark__name .big{font-size:70px;letter-spacing:1px;text-transform:uppercase}
  .front-mark__name .small{font-size:24px;letter-spacing:1px;text-transform:uppercase;margin-top:6px}

  .back-mark{position:absolute;left:0;right:0;top:48px;display:flex;flex-direction:column;align-items:center;color:var(--brown);font-weight:600;line-height:1}
  .back-mark__dot{width:70px;height:70px;border-radius:50%;background:var(--brown);margin-bottom:16px}
  .back-mark .big{font-size:44px;text-transform:uppercase;letter-spacing:1px}
  .back-mark .small{font-size:17px;text-transform:uppercase;letter-spacing:1px;margin-top:6px}

  .owner-name{position:absolute;left:0;right:0;top:340px;font-size:37px;font-weight:600;color:var(--brown);line-height:42px;letter-spacing:.5px}
  .owner-role{position:absolute;left:0;right:0;top:379px;font-size:18px;line-height:22px;letter-spacing:.5px}
  .tagline{position:absolute;left:0;right:0;top:412px;font-size:18px;line-height:25px;letter-spacing:.6px}
  .divider{position:absolute;left:0;right:0;display:flex;justify-content:center;align-items:center;gap:5px}
  .divider--phone{top:471px}
  .divider--pin{top:542px}
  .divider span{display:block;border-radius:50%;background:var(--brown)}
  .divider .icon{width:22px;height:22px;display:flex;align-items:center;justify-content:center;margin:0 4px}
  .contact{position:absolute;left:0;right:0;font-size:18px;line-height:22px;letter-spacing:.6px}
  .contact--phone{top:501px}
  .contact--address{top:571px}
  .pitch{position:absolute;left:15px;top:611px;width:392px;height:82px;border:2.5px solid #000;border-radius:12px;font-size:17.5px;line-height:24px;letter-spacing:.5px;display:flex;align-items:center;justify-content:center;padding:0 4px;white-space:nowrap}
</style>
</head>
<body>
  <section class="card card--front" aria-label="Card front">
    <div class="front-mark">
      <div class="front-mark__dot"></div>
      <div class="front-mark__name"><span class="big">Tolbek</span><span class="small">Builders LLC</span></div>
    </div>
  </section>

  <section class="card card--back" aria-label="Card back">
    <div class="back-mark">
      <div class="back-mark__dot"></div>
      <span class="big">Tolbek</span>
      <span class="small">Builders LLC</span>
    </div>

    <h1 class="owner-name">Dale Whitacre</h1>
    <p class="owner-role">Owners</p>
    <p class="tagline">Committed to Quality,<br>Service, and Integrity</p>

    <div class="divider divider--phone">
      <span style="width:5px;height:5px"></span><span style="width:6px;height:6px"></span><span style="width:7px;height:7px"></span><span style="width:9px;height:9px"></span><span style="width:10px;height:10px"></span><span style="width:11px;height:11px"></span><span style="width:12px;height:12px"></span><span style="width:14px;height:14px"></span>
      <span class="icon"><svg width="22" height="22" viewBox="0 0 22 22"><circle cx="11" cy="11" r="11" fill="var(--brown)"/><path d="M7.5 6.5l2 2-1 1.3a6 6 0 0 0 2.7 2.7l1.3-1 2 2-1.2 1.4c-3.4-.3-6.9-3.8-7.2-7.2z" fill="#fff"/></svg></span>
      <span style="width:14px;height:14px"></span><span style="width:12px;height:12px"></span><span style="width:11px;height:11px"></span><span style="width:10px;height:10px"></span><span style="width:9px;height:9px"></span><span style="width:7px;height:7px"></span><span style="width:6px;height:6px"></span><span style="width:5px;height:5px"></span>
    </div>
    <p class="contact contact--phone">610-555-0187</p>

    <div class="divider divider--pin">
      <span style="width:5px;height:5px"></span><span style="width:6px;height:6px"></span><span style="width:7px;height:7px"></span><span style="width:9px;height:9px"></span><span style="width:10px;height:10px"></span><span style="width:11px;height:11px"></span><span style="width:12px;height:12px"></span><span style="width:14px;height:14px"></span>
      <span class="icon"><svg width="22" height="22" viewBox="0 0 22 22"><circle cx="11" cy="11" r="11" fill="var(--brown)"/><path d="M11 5a3.5 3.5 0 0 0-3.5 3.5c0 2.6 3.5 6 3.5 6s3.5-3.4 3.5-6A3.5 3.5 0 0 0 11 5z" fill="none" stroke="#fff" stroke-width="1.2"/><circle cx="11" cy="8.5" r="1.2" fill="#fff"/><ellipse cx="11" cy="16" rx="3" ry="1" fill="none" stroke="#fff" stroke-width="1"/></svg></span>
      <span style="width:14px;height:14px"></span><span style="width:12px;height:12px"></span><span style="width:11px;height:11px"></span><span style="width:10px;height:10px"></span><span style="width:9px;height:9px"></span><span style="width:7px;height:7px"></span><span style="width:6px;height:6px"></span><span style="width:5px;height:5px"></span>
    </div>
    <p class="contact contact--address">4076 Copper Ridge RD, Carvell, OH 43912</p>

    <p class="pitch">"Are you thinking about a new building<br>on your property, or renovating an<br>existing structure? Contact".....</p>
  </section>
</body>
</html>
```